Coaching landingpage/salespage need a layout

Hi!
We are two people from Sweden looking for help to design our coaching landingpage/salespage.

What about:
We need a nice modern timeless appealing Photoshop layout (landingpage) for our coaching page where we coach people to “how to get a richer lifestyle”.

Style of page:
We want the site to reflect seriousness but still harmonic. We would like somewhat colorful and (but not too crazy). After all, we are coaching about investments and private economy.
Responsive layout – consider stacking order when scaling down window width. Fullpage-design where content areas are 960 grid/max-width.

----------------------------------------------------------------------------
Content on page:
*Headersection – Logo and header image with the two coaches together and space for later on adding a video.

*On the landingpage the customers can read up on what we mean by a richer lifestyle (use dummy text). We show our Vardagskompassen (= Lifestyle matrix) and a little description about that. If the customers want to know more, they can click "read more (or a symbolic icon that relates to read more)" to expand a hidden div (section) where they can read more about Vardagskompassen. They can also minimize the section.

*3-4 Unique selling points “Four reasons why choose coaching” with nice designed number-icons and some place for text.

*The customer should also be able to read something about what happens during a typical coaching session, some bullets that summarize it (use dummy text) and a couple of headlines, maybe 3 or 4 (about what they need to prepare for themselves .eg Skype, headset/microphone etc).

*Offer/product section: A section where the customer can see what services we provide, choose product and click order. When customer click order they will arrive to an order-page (this one you don’t have to design) .
Our products are as followed: Bronze (single coaching session), Silver (small-package), Gold (large-package). Use provided graphics for these products.

*Testimonials section. Currently we have 2 good testimonials, but only with text no portrait picture.

Testimonial1: “Uppiggande och inspirerande! Kommer med enkla vardagstips såväl som svårare tips. Ett roligt sätt att få en spark i baken, så att ekonomi-energin bibehålls! Tack för ett bra samtal!" - Helena Brattvik

Testimonial2: "Värdefullast för mig var kunskapen om alternativa investeringssställen som inte är börs eller eget ägande." - Annika Sjöstedt

*Section with portraits and info about the coaches (currently 2 coaches, but in future will be several, so a design-section that’s lets us add more coaches).

*Footer-section
------------------------------------------------------------------------

Colors:
Use Vardagskompassen (attached file) as colorinspiration. Doesn’t have to be exactly those colors, you can use similar colors if it is more pleasing to the eye and you can also use complementary colors.

Currently we have tried of our own but don't really nail it with any apealing design. This is what we have done so far but we want to replace it with your more professional design:

https://www.harborkite.se/full/Page/coaching13
-------------------------------------------------------------

SUMMARIZE of the above design-description:

* Our logo (attached psd-file with smart-object. You can try different colors with color-overlay)

*Apealing headerimage with portrait (attached file "big_portrait")

*Introduction text (use dummy text about 100 words)

*Text about Vardagskompassen (use dummy text about 200 words)

*Vardagskompassen (attached psd-file with smart-object)

*What we are covering during a coaching session (dummy text about 200 words and about 5 or 6 bullets)

*3-4 Unique Selling Points with stylish number icons (not 2 small) and some text.
*Our offers Bronze, Silver, Gold (attached pictures)
*Testimonials
*Picture & info about coaches (attached pictures, choose whichever suits you)
*Footer

Please comment if there are questions.

Target Market(s)

People who want to learn how to create a richer lifestyle which involves more freedom and a better well-being

Number of Pages Required

1 page

Font styles to use
Sans Serif
Other font styles liked:
• Roboto

Requirements
Should not have
• A cheezy unmodern landingpage with lots of texts and 10 sign-up buttons.
• This page is not a site about capturing emails and building lists by provide a "best-guide-for-something". It´s about getting people to book and pay for one or more coaching-sessions.

```html
<!DOCTYPE html>
<html lang="sv">
<head>
<meta charset="utf-8">
<title>Harbor Kite – Coaching</title>
<link href="https://fonts.googleapis.com/css2?family=Montserrat:wght@400;600;700&family=Open+Sans:ital,wght@0,400;0,600;1,400&display=swap" rel="stylesheet">
<style>
:root{
  --blue:#3fa9dc;
  --blue-deep:#2f86c6;
  --ink:#1f1f1f;
  --body:#444;
  --line:#d4d4d4;
  --night:#121212;
  --footer:#3a87c9;
  --grey-band:#ececec;
  --bronze:#c9753a;
  --gold:#e7b422;
  --silver:#bdbdbd;
  --q-blue:#2ea3dc;
  --q-orange:#f5a623;
  --q-brown:#9a8c7a;
  --q-green:#3dae5a;
}
*{box-sizing:border-box;margin:0;padding:0}
html,body{width:1200px;height:3358px;overflow:hidden}
body{position:relative;background:#fff;font-family:"Open Sans",Arial,sans-serif;color:var(--body)}
.abs{position:absolute}
.heading{font-family:"Montserrat",Arial,sans-serif;font-weight:600;color:var(--ink);font-size:30px;line-height:38px}
.heading span{color:var(--blue);font-weight:400}
.heading-rule{position:absolute;height:1px;background:var(--line)}
.heading-mark{position:absolute;width:12px;height:12px;background:var(--blue)}
.btn{position:absolute;display:flex;align-items:center;justify-content:center;gap:10px;border:2px solid #333;font-size:12px;color:#222;background:#fff;font-family:"Montserrat",Arial,sans-serif;white-space:nowrap}
.btn svg{width:17px;height:17px;flex:none}

/* header */
.site-header{left:0;top:0;width:1200px;height:92px;border-bottom:2px solid var(--blue-deep)}
.brand{left:99px;top:28px;display:flex;align-items:center;gap:12px;font-family:"Montserrat",Arial,sans-serif;font-size:24px;color:var(--blue-deep);letter-spacing:2px}
.brand-square{width:28px;height:28px;background:var(--blue-deep)}
.call{left:862px;top:26px;display:flex;gap:12px;align-items:center}
.call small{display:block;font-size:10px;font-weight:700;color:#222;font-family:"Montserrat",Arial,sans-serif}
.call b{font-size:20px;font-weight:400;color:#444;letter-spacing:1px;line-height:24px}
.social-square{left:1068px;top:28px;width:32px;height:32px;background:#3b5998}

/* hero */
.hero{left:0;top:92px;width:1200px;height:513px;background:linear-gradient(110deg,#f4f4f4 0%,#d8d8d8 45%,#9a9a9a 70%,#3c3c3c 100%)}
.hero-kicker{left:99px;top:288px;font-family:"Montserrat",Arial,sans-serif;font-size:27px;color:#222}
.hero-title{left:97px;top:324px;font-family:"Montserrat",Arial,sans-serif;font-size:42px;font-weight:600;color:#111}
.hero-btn{left:99px;top:398px;width:166px;height:40px;background:var(--blue);color:#fff;font-size:13px;font-family:"Montserrat",Arial,sans-serif;display:flex;align-items:center;justify-content:center;gap:10px}

/* about */
.about-text{left:99px;top:766px;width:612px;font-size:11.5px;line-height:22px;color:#444}
.matrix{left:786px;top:690px;width:282px;height:300px;border-radius:10px;background:linear-gradient(135deg,var(--q-blue) 0%,var(--q-orange) 35%,var(--q-brown) 65%,var(--q-green) 100%)}

/* why */
.why{left:0;top:1066px;width:1200px;height:479px;background:linear-gradient(180deg,#49b2e4,#3aa1d8)}
.why-frame{left:110px;top:1241px;width:360px;height:234px;border:2px dotted #e8f6ff;padding:8px}
.why-art{width:100%;height:100%;background:linear-gradient(135deg,#ffffff 0%,#dfe6ee 45%,#1f6fc4 55%,#e9eef4 100%)}
.why-list{left:526px;top:1252px;width:570px;list-style:none;color:#fff;font-size:12.5px;line-height:21px}
.why-list li{position:relative;padding-left:26px;margin-bottom:22px}
.why-list li::before{content:"";position:absolute;left:0;top:5px;border-left:9px solid #fff;border-top:5px solid transparent;border-bottom:5px solid transparent}

/* products */
.medal{position:absolute;width:140px;height:140px;border-radius:50%}
.medal::after{content:"";position:absolute;inset:14px;border-radius:50%;border:3px solid rgba(255,255,255,.35)}
.product-name{position:absolute;width:260px;text-align:center;font-family:"Montserrat",Arial,sans-serif;font-weight:600;font-size:16px;color:#222}
.product-sub{position:absolute;width:260px;text-align:center;font-size:12px;color:#555}

/* testimonials */
.testimonials{left:0;top:2082px;width:1200px;height:415px;background:var(--grey-band)}
.avatar{position:absolute;width:92px;height:92px;border-radius:50%;background:#dde7e4;border:3px solid #fff}
.bubble{position:absolute;background:#fff;border:1px solid #ddd;padding:14px 20px 12px 50px;font-size:11.5px;line-height:18px;color:#555;font-style:italic;text-align:center}
.bubble::before{content:"\201C";position:absolute;left:16px;top:6px;font-size:44px;color:#ccc;font-style:normal;font-family:Georgia,serif}
.bubble::after{content:"";position:absolute;left:-11px;top:30px;width:20px;height:20px;background:#fff;border-left:1px solid #ddd;border-bottom:1px solid #ddd;transform:rotate(45deg)}
.client{position:absolute;font-size:12px;font-weight:600;color:#333}

/* coaches */
.coach-photo{position:absolute;width:264px;height:215px;box-shadow:8px 8px 0 #e2e2e2}
.coach-name{position:absolute;font-family:"Montserrat",Arial,sans-serif;font-weight:600;font-size:14px;color:#222}
.coach-bio{position:absolute;width:270px;font-size:11.5px;line-height:22px;color:#555}

/* footer */
.footer-nav{left:0;top:3168px;width:1200px;height:70px;background:var(--night);color:#fff;font-family:"Montserrat",Arial,sans-serif;font-size:13px}
.footer-nav ul{list-style:none;display:flex;gap:40px;position:absolute;left:106px;top:26px}
.footer-nav li+li::before{content:"|";margin-right:40px}
.footer-nav .social-square{left:1060px;top:24px;width:22px;height:22px}
.footer-info{left:0;top:3238px;width:1200px;height:120px;background:var(--footer);color:#fff;font-size:11.5px}
.info-item{position:absolute;top:30px;display:flex;gap:12px}
.info-icon{width:34px;height:34px;border-radius:50%;background:#fff;display:flex;align-items:center;justify-content:center;flex:none}
.info-item b{display:block;font-family:"Montserrat",Arial,sans-serif;font-size:12px}
.footer-brand{left:846px;top:28px;display:flex;align-items:center;gap:10px;font-family:"Montserrat",Arial,sans-serif;font-size:22px;letter-spacing:2px}
.footer-brand i{width:26px;height:26px;background:#fff}
.copyright{left:846px;top:76px;font-size:11px}
</style>
</head>
<body>

<header class="site-header abs">
  <div class="brand abs"><span class="brand-square"></span>HARBOR KITE</div>
  <div class="call abs">
    <svg width="30" height="30" viewBox="0 0 24 24"><path d="M6.6 10.8a15 15 0 0 0 6.6 6.6l2.2-2.2c.3-.3.7-.4 1-.2 1.1.4 2.3.6 3.6.6.6 0 1 .4 1 1V20c0 .6-.4 1-1 1A17 17 0 0 1 3 4c0-.6.4-1 1-1h3.5c.6 0 1 .4 1 1 0 1.3.2 2.5.6 3.6.1.3 0 .7-.2 1z" fill="#333"/></svg>
    <div><small>CALL US NOW!</small><b>(031) 555 0192</b></div>
  </div>
  <div class="social-square abs"></div>
</header>

<section class="hero abs" role="img" aria-label="Header photo of the two coaches standing together in dark jackets against a soft grey backdrop"></section>
<div class="hero-kicker abs">Step By Step To</div>
<div class="hero-title abs">A Richer Lifestyle</div>
<div class="hero-btn abs">Watch Our Video
  <svg width="17" height="17" viewBox="0 0 20 20"><circle cx="10" cy="10" r="8.5" fill="none" stroke="#fff" stroke-width="1.6"/><path d="M8 6l5 4-5 4z" fill="#fff"/></svg>
</div>

<!-- about -->
<h2 class="heading abs" style="left:99px;top:688px">Know About <span>Harbor Kite</span></h2>
<div class="heading-rule" style="left:99px;top:746px;width:612px"></div>
<div class="heading-mark" style="left:99px;top:735px"></div>
<p class="about-text abs">Lorem ipsum dolor sit amet, consectetuer adipiscing elit, sed diam nonummy nibh euismod tincidunt ut laoreet dolore magna aliquam erat volutpat. Ut wisi enim ad minim veniam, quis nostrud exerci tation ullamcorper suscipit lobortis nisl ut aliquip ex ea commodo consequat. Duis autem vel eum iriure dolor in hendrerit in vulputate velit esse molestie consequat, vel illum dolore eu feugiat nulla facilisis at vero eros et accumsan et iusto odio dignissim qui blandit praesent luptatum zzril nulla facilisis at vel illum dolore vero eros et odio delenit nulla facilisi.</p>
<div class="btn" style="left:99px;top:932px;width:128px;height:36px">Read More
  <svg viewBox="0 0 20 20"><circle cx="10" cy="10" r="8.5" fill="none" stroke="#222" stroke-width="1.6"/><path d="M6 10h8M11 7l3 3-3 3" fill="none" stroke="#222" stroke-width="1.6"/></svg>
</div>

<div class="matrix abs" role="img" aria-label="Vardagskompassen lifestyle matrix illustration with four coloured quadrants and two axis arrows"></div>

<!-- why -->
<section class="why abs"></section>
<h2 class="heading abs" style="left:0;width:1200px;text-align:center;top:1128px;color:#fff">Why <span style="color:#e4f5ff">Choose Coaching</span></h2>
<div class="heading-rule" style="left:430px;top:1184px;width:340px;background:rgba(255,255,255,.5)"></div>
<div class="heading-mark" style="left:594px;top:1173px;background:#fff"></div>
<div class="why-frame abs"><div class="why-art" role="img" aria-label="Illustration of blue puzzle pieces spelling the word coaching"></div></div>
<ul class="why-list abs">
  <li>Lorem ipsum dolor sit amet, consectetuer adipiscing elit, sed diam nonummy nibh tincidunt ut laoreet.</li>
  <li>Ut wisi enim ad minim veniam, quis nostrud exerci tation ullamcorper suscipit ut aliquip.</li>
  <li>Accumsan et iusto odio dignissim qui blandit praesent luptatum zzril nulla facilisis at vel illum dolore in vulputate.</li>
  <li>Commodo consequat. Duis autem vel eum iriure dolor in hendrerit in vulputate velit consequat ullamcorper suscipit.</li>
</ul>

<!-- products -->
<h2 class="heading abs" style="left:0;width:1200px;text-align:center;top:1626px">Our <span>Products</span></h2>
<div class="heading-rule" style="left:400px;top:1682px;width:400px"></div>
<div class="heading-mark" style="left:594px;top:1671px"></div>

<div class="medal" style="left:196px;top:1721px;background:radial-gradient(circle at 35% 30%,#f1a66a,var(--bronze) 55%,#8e4a1d)"></div>
<div class="medal" style="left:530px;top:1721px;background:radial-gradient(circle at 35% 30%,#fde27a,var(--gold) 55%,#b17d07)"></div>
<div class="medal" style="left:855px;top:1721px;background:radial-gradient(circle at 35% 30%,#f4f4f4,var(--silver) 55%,#8a8a8a)"></div>

<div class="product-name" style="left:136px;top:1906px">Bronze</div>
<div class="product-sub" style="left:136px;top:1930px">Single Coaching Session</div>
<div class="product-name" style="left:470px;top:1906px">Gold</div>
<div class="product-sub" style="left:470px;top:1930px">Small - Package</div>
<div class="product-name" style="left:795px;top:1906px">Silver</div>
<div class="product-sub" style="left:795px;top:1930px">Large - Package</div>

<div class="btn" style="left:174px;top:1967px;width:186px;height:34px">Make An Appointment <svg viewBox="0 0 20 20"><circle cx="10" cy="10" r="8.5" fill="none" stroke="#222" stroke-width="1.6"/><path d="M6 10h8M11 7l3 3-3 3" fill="none" stroke="#222" stroke-width="1.6"/></svg></div>
<div class="btn" style="left:508px;top:1967px;width:186px;height:34px">Make An Appointment <svg viewBox="0 0 20 20"><circle cx="10" cy="10" r="8.5" fill="none" stroke="#222" stroke-width="1.6"/><path d="M6 10h8M11 7l3 3-3 3" fill="none" stroke="#222" stroke-width="1.6"/></svg></div>
<div class="btn" style="left:833px;top:1967px;width:186px;height:34px">Make An Appointment <svg viewBox="0 0 20 20"><circle cx="10" cy="10" r="8.5" fill="none" stroke="#222" stroke-width="1.6"/><path d="M6 10h8M11 7l3 3-3 3" fill="none" stroke="#222" stroke-width="1.6"/></svg></div>

<!-- testimonials -->
<section class="testimonials abs" role="img" aria-label="Faint background wall of many small client portraits"></section>
<h2 class="heading abs" style="left:0;width:1200px;text-align:center;top:2143px">Client <span>Testimonial</span></h2>
<div class="heading-rule" style="left:400px;top:2199px;width:400px"></div>
<div class="heading-mark" style="left:594px;top:2188px"></div>

<div class="avatar" role="img" aria-label="Placeholder avatar for the client" style="left:100px;top:2273px"></div>
<div class="bubble" style="left:210px;top:2268px;width:366px;height:99px">Uppiggande och inspirerande! Kommer med enkla vardagstips såväl som svårare tips. Ett roligt sätt att få en spark i baken, så att ekonomi-energin bibehålls! Tack för ett bra samtal!</div>
<div class="client" style="left:244px;top:2392px">Mr. Helena Brattvik</div>

<div class="avatar" role="img" aria-label="Placeholder avatar for the client" style="left:626px;top:2273px"></div>
<div class="bubble" style="left:738px;top:2268px;width:362px;height:99px">Värdefullast för mig var kunskapen om alternativa investeringssställen som inte är börs eller eget ägande.</div>
<div class="client" style="left:772px;top:2392px">Mr. Annika Sjöstedt</div>

<!-- coaches -->
<h2 class="heading abs" style="left:0;width:1200px;text-align:center;top:2584px">Our <span>Coaches</span></h2>
<div class="heading-rule" style="left:400px;top:2640px;width:400px"></div>
<div class="heading-mark" style="left:594px;top:2629px"></div>

<div class="coach-photo" role="img" aria-label="Portrait photo of coach Joakim outdoors" style="left:99px;top:2682px;background:linear-gradient(160deg,#7fa3c7,#6a8a52 60%,#3e5a2c)"></div>
<div class="coach-photo" role="img" aria-label="Portrait photo of coach Henrik in a dark suit" style="left:466px;top:2682px;background:linear-gradient(160deg,#7d7268,#3a3330 60%,#1c1a19)"></div>
<div class="coach-photo" role="img" aria-label="Placeholder avatar on a yellow background" style="left:826px;top:2682px;background:linear-gradient(160deg,#f7d23a,#f0c419)"></div>

<div class="coach-name" style="left:99px;top:2925px">Mr. Joakim Lindqvist</div>
<p class="coach-bio" style="left:99px;top:2950px">Mångsidig investerare med fokus på alternativa och högriskinvesteringar. Förutom börsen investerar Joakim i onoterade startup-bolag och olika internetbaserade investeringar såsom P2P-lending, onlinespel och appar.</p>
<div class="coach-name" style="left:466px;top:2925px">Mr. Henrik Dalsjö</div>
<p class="coach-bio" style="left:466px;top:2950px">Henrik har en bred bakgrund inom ekonomi och IT. Som investerare ligger hans fokus på utdelningsaktier, fastigheter och internetbaserat entreprenörskap. Han har också en lång erfarenhet och en stor passion av att hjälpa människor...[+]</p>
<div class="coach-name" style="left:826px;top:2925px">Mr. Lorem ipsum</div>
<p class="coach-bio" style="left:826px;top:2950px">Lorem ipsum dolor sit amet, conse adipiscing elit, sed diam nonummy nibh euis tincidunt ut laoreet dolore magna aliquam erat nibhup magna diam nonummy nibh euis tincidunt ut laoreet dolore magna volutpat....[+]</p>

<!-- footer -->
<nav class="footer-nav abs">
  <ul><li>BLOG</li><li>COACHING</li><li>ABOUT US</li></ul>
  <div class="social-square abs"></div>
</nav>
<footer class="footer-info abs">
  <div class="info-item" style="left:100px">
    <span class="info-icon"><svg width="16" height="16" viewBox="0 0 24 24"><path d="M12 2a7 7 0 0 0-7 7c0 5 7 13 7 13s7-8 7-13a7 7 0 0 0-7-7zm0 9.5A2.5 2.5 0 1 1 12 6.5a2.5 2.5 0 0 1 0 5z" fill="#222"/></svg></span>
    <div><b>HARBOR KITE</b>Harbor Kite AB Ekvägen 12<br>411 05 Göteborg</div>
  </div>
  <div class="info-item" style="left:384px">
    <span class="info-icon"><svg width="16" height="16" viewBox="0 0 24 24"><path d="M6.6 10.8a15 15 0 0 0 6.6 6.6l2.2-2.2c.3-.3.7-.4 1-.2 1.1.4 2.3.6 3.6.6.6 0 1 .4 1 1V20c0 .6-.4 1-1 1A17 17 0 0 1 3 4c0-.6.4-1 1-1h3.5c.6 0 1 .4 1 1 0 1.3.2 2.5.6 3.6.1.3 0 .7-.2 1z" fill="#222"/></svg></span>
    <div><b>CALL US :</b><span style="font-size:14px;font-weight:600">031. 555. 0193</span></div>
  </div>
  <div class="info-item" style="left:598px">
    <span class="info-icon"><svg width="16" height="16" viewBox="0 0 24 24"><path d="M3 6h18v12H3z" fill="#222"/><path d="M3 6l9 7 9-7" fill="none" stroke="#fff" stroke-width="1.5"/></svg></span>
    <div><b>EMAIL US :</b>team@harborkite.se</div>
  </div>
  <div class="footer-brand abs"><i></i>HARBOR KITE</div>
  <div class="copyright abs">© 2016 Harborkite. All Rights Reserved.</div>
</footer>

</body>
</html>
```